Calvanto Group Real Estate Company business cards

New business card design, we are generally happy with the basic layout of the existing front of business card, (feel free to change) but require a head shot photo on the back side.

http://www.calvanto.com.au/

Attached logos, and existing business card

------------------------------

Target Market(s)

Real estate

Industry/Entity Type

Real Estate

Contact Information for Business Card

Standard size double sided

Font styles to use
Other font styles liked:
• Futura

Requirements
Must have
• Photo head shot on the back side
Nice to have
• yes
Should not have
• No

```html
<!DOCTYPE html>
<html lang="en">
<head>
<meta charset="utf-8">
<title>Calvanto Group – Business Cards</title>
<link href="https://fonts.googleapis.com/css2?family=Jost:wght@400;500&family=Roboto:wght@400&family=Roboto+Condensed:wght@700&display=swap" rel="stylesheet">
<style>
  :root {
    --bg: #e6e6e8;
    --purple: #3a1a63;
    --purple-deep: #2a1049;
    --orange: #f08a1c;
    --white: #ffffff;
    --ink: #2a1a45;
  }
  * { margin: 0; padding: 0; box-sizing: border-box; }
  html, body { width: 1200px; height: 1200px; overflow: hidden; background: var(--bg); }
  .canvas { position: relative; width: 1200px; height: 1200px; }

  .card {
    position: absolute; left: 220px; width: 760px; height: 440px;
    border-radius: 26px; overflow: hidden;
    box-shadow: 0 10px 24px rgba(0,0,0,0.18);
  }

  /* Front */
  .card--front { top: 140px; background: linear-gradient(160deg, var(--purple) 0%, var(--purple-deep) 100%); }
  .tagline {
    position: absolute; left: 52px; top: 150px;
    font-family: "Jost", sans-serif; font-weight: 400; font-size: 38px; line-height: 1.15;
    color: var(--white);
  }
  .tagline .accent { color: var(--orange); }
  .wordmark { position: absolute; font-family: "Jost", sans-serif; font-weight: 500; line-height: 1; }
  .wordmark .name { display: block; }
  .wordmark .group { display: block; text-align: right; letter-spacing: 0.45em; }
  .card--front .wordmark { left: 52px; top: 318px; color: var(--white); }
  .card--front .wordmark .name { font-size: 64px; }
  .card--front .wordmark .group { font-size: 12px; margin-top: 4px; }
  .headshot {
    position: absolute; left: 396px; top: 22px; width: 342px; height: 396px;
    background: linear-gradient(180deg, #f4f4f6 0%, #e9e9ee 55%, #3b4766 100%);
  }

  /* Back */
  .card--back { top: 640px; background: var(--white); }
  .accent-band {
    position: absolute; inset: 0;
    clip-path: polygon(100% 30%, 100% 100%, 0 100%, 0 92%);
    background: linear-gradient(160deg, #4a2478 0%, var(--purple) 50%, var(--purple-deep) 100%);
  }
  .card--back .wordmark { left: 48px; top: 62px; color: var(--purple); }
  .card--back .wordmark .name { font-size: 84px; }
  .card--back .wordmark .group { font-size: 14px; margin-top: 4px; }
  .person { position: absolute; left: 54px; top: 196px; }
  .person__name {
    font-family: "Roboto Condensed", sans-serif; font-weight: 700; font-size: 28px;
    color: var(--orange); letter-spacing: 0.02em;
  }
  .person__role, .person__abn { font-family: "Roboto", sans-serif; font-size: 17px; color: var(--ink); }
  .person__role { margin-top: 6px; }
  .person__abn { margin-top: 30px; }
  .contact {
    position: absolute; right: 34px; top: 270px; list-style: none;
    font-family: "Roboto", sans-serif; font-size: 17px; color: var(--white); text-align: right;
  }
  .contact li { display: flex; justify-content: flex-end; align-items: center; gap: 12px; height: 30px; }
  .contact svg { width: 18px; height: 18px; }
</style>
</head>
<body>
<div class="canvas">

  <section class="card card--front">
    <p class="tagline">Let us<br>show you<br><span class="accent">property</span></p>
    <div class="wordmark"><span class="name">calvanto</span><span class="group">GROUP</span></div>
    <div class="headshot" role="img" aria-label="Head shot photo of the agent in a suit"></div>
  </section>

  <section class="card card--back">
    <div class="accent-band" role="img" aria-label="Decorative purple and orange swoosh band"></div>
    <div class="wordmark"><span class="name">calvanto</span><span class="group">GROUP</span></div>
    <div class="person">
      <p class="person__name">DANIEL TRAN</p>
      <p class="person__role">Director</p>
      <p class="person__abn">ABN: 41 208 663 957</p>
    </div>
    <ul class="contact">
      <li>0412 555 318
        <svg viewBox="0 0 18 18"><rect x="4" y="1" width="10" height="16" rx="2" fill="none" stroke="#fff" stroke-width="2"/><circle cx="9" cy="14" r="1" fill="#fff"/></svg></li>
      <li>www.calvanto.com.au
        <svg viewBox="0 0 18 18"><circle cx="9" cy="9" r="7.5" fill="none" stroke="#fff" stroke-width="1.6"/><ellipse cx="9" cy="9" rx="3.2" ry="7.5" fill="none" stroke="#fff" stroke-width="1.4"/><line x1="1.5" y1="9" x2="16.5" y2="9" stroke="#fff" stroke-width="1.4"/></svg></li>
      <li>daniel.tran@calvanto.com.au
        <svg viewBox="0 0 18 18"><rect x="1" y="3.5" width="16" height="11" fill="none" stroke="#fff" stroke-width="1.6"/><path d="M1,3.5 L9,10 L17,3.5" fill="none" stroke="#fff" stroke-width="1.6"/></svg></li>
    </ul>
  </section>

</div>
</body>
</html>
```